Lotstallmart.com Webpage Design

Design Brief for lotstallmart.com (Copy of Brief also in attached Word file)

Name of Website- lotstallmart.com (existing logo and look & feel of website to be changed)

Logo - Finalised. The logo files are attached with the brief as “logo.jpeg”. The “Blue- Grey” version of the logo is for use on lighter backgrounds and the “Orange-White” version of the logo is for use on darker backgrounds. (A full Black version of the logo is also attached). Both versions may be used in different parts of the website. All attached files are in .png format.
Status - The website in functional and is undergoing user trials. However, we want to improve the look & feel of the website so at it seems
a. cotemporary,
b. Easy to Navigate
c. professional and
d. Vibrant.

Please visit ‘lotstallmart.com’ to check out the website and its functionalities – please use it only as a reference for the features & functions to be provided, however the designer should use a ‘Free Hand’ in designing the composition of various parts of the webpage without getting too influenced by the existing design

Objective of the Website ‘lotstallmart.com –
a. It is a portal focussed on listing of ‘Retail’ specific real-estate properties by developers, owners and realty brokers. The properties shall listed under the following four categories-
i. Retail Malls
ii. Shopping Complexes
iii. High-street shops
iv. Retail Warehouses
*refer lotstallmart.com for better clarity

b. The abovementioned properties shall be listed either for ‘Sale’ or ‘rent\lease’ or both

c. Users shall visit the site in case they wish to acquire a retail \ shop space either on ‘sale’ or ‘rent’. These Users would be able to specify the ‘Search Criteria’ through the tool-bars provided on the website – the ‘Search Criteria’ shall comprise of ‘Type of space category’, ‘City’, ‘Locality’, transaction type ie ‘Rent \ Sale’ and ‘Area Range’

d. The main revenue model for the website shall be listing fee ( or advertising charges ) payable by those listing their properties on the website.

Three Main Pages of Website (lotstallmart.com) that need to be designed -
a. Main Home Page (visit the web link - http://lotstallmart.com/ ) - The main home page has the “Search Toolbar” for specifying of Search Criteria by the User. It shall also have the following features & functions-
i. Main Advertising Banner
ii. Featured Projects
iii. New Launches
iv. Toolbar with buttons – ‘Advertise with Us’, ‘Listings Alert’, ‘Mart Wizards’, ‘Advertiser Login’

b. Property Listings Page (visit the web link - http://lotstallmart.com/gurgaon-in-india ) - The List of property options that match the Criteria specified by the ‘User’ get displayed on this page.

c. Property Detail Page - When the ‘User’ clicks on the “More….” Button on the ‘Property Listings Page’ (given in point b. above) the web page with the details of the property opens. (For Example – visit the web link - http://lotstallmart.com/vorne-Shopping-Complex-vorne-quadrion-gurgaon-636 )

Note:- Please refer to attached ‘Shopping’ related images the designer may use them on the website to provide a look & feel of retail if required – either separately or rotate in a single window

Target Market(s)

Retailers & Investors looking for retail space, Real Estate Brokers, Developers

Industry/Entity Type

Advertising

Number of Pages Required

3 page

Requirements
Must have
• Refer to existing site lotstallmart.com -- all the existing functionalities are a must have.
Nice to have
• The Designer may use the retail related images on the website if required for making it more vibrant. Refer attached images Shopping(1-6).jpg

```html
<!DOCTYPE html>
<html lang="en">
<head>
<meta charset="utf-8">
<title>Lotstallmart.com – Retail Space Portal</title>
<link href="https://fonts.googleapis.com/css2?family=Lato:wght@400;700;900&display=swap" rel="stylesheet">
<style>
:root{
  --blue:#2b87dc;
  --blue-dark:#1f6fbd;
  --navy:#173a5e;
  --ink:#2e2e2e;
  --muted:#6b6b6b;
  --line:#d9d9d9;
  --panel:#f2f2f2;
  --footer:#efefef;
  --black-band:#1e1e1e;
  --white:#ffffff;
  --btn-grey:#e4e4e4;
}
*{box-sizing:border-box;margin:0;padding:0}
html,body{width:1200px;height:2568px;overflow:hidden}
body{font-family:"Lato",Arial,sans-serif;color:var(--ink);background:var(--white);position:relative}
.abs{position:absolute}

/* header */
.site-header{position:absolute;left:0;top:0;width:1200px;height:88px;background:var(--white)}
.brand{position:absolute;left:154px;top:24px;display:flex;align-items:center;gap:10px;font-weight:900;font-size:30px;color:var(--blue);letter-spacing:-.5px}
.brand-dot{width:30px;height:30px;border-radius:50%;background:var(--navy)}
.top-nav a{position:absolute;top:29px;height:34px;line-height:34px;text-align:center;font-size:13px;color:#333;background:var(--btn-grey);text-decoration:none}
.top-nav .login{background:var(--blue);color:var(--white);font-weight:700}

/* hero */
.hero{position:absolute;left:0;top:88px;width:1200px;height:504px;background:linear-gradient(100deg,#5b2a1e 0%,#a3553a 25%,#d9c3a2 50%,#7b6a5c 75%,#3d3a38 100%)}
.hero-dots{position:absolute;left:925px;top:38px;display:flex;gap:8px}
.hero-dots span{width:14px;height:14px;border-radius:50%;border:2px solid var(--white)}
.hero-dots span.on{border-color:var(--blue)}
.mode-tabs{position:absolute;left:151px;top:66px;width:49px}
.mode-tabs div{color:var(--white);font-size:13px;font-weight:700;writing-mode:vertical-rl;transform:rotate(180deg);display:flex;align-items:center;justify-content:center}
.mode-tabs .sale{height:68px;background:#3a3a3a}
.mode-tabs .rent{height:138px;background:#5a5a5a}
.search-panel{position:absolute;left:200px;top:39px;width:344px;height:443px;background:#f4f4f4}
.field{position:absolute;left:22px;width:304px;height:44px;background:var(--white);border:1px solid var(--line);font-size:12px;color:#666;padding:0 14px;line-height:42px}
.field svg{position:absolute;right:12px;top:18px}
.search-btn{position:absolute;left:22px;top:360px;width:304px;height:41px;background:var(--blue);color:var(--white);font-weight:700;font-size:14px;text-align:center;line-height:41px;letter-spacing:.5px}

/* categories */
.categories{position:absolute;left:0;top:592px;width:1200px;height:298px;background:var(--blue)}
.section-title{position:absolute;left:0;width:1200px;text-align:center;font-size:22px;font-weight:700;letter-spacing:.5px}
.categories .section-title{top:38px;color:var(--white)}
.cat{position:absolute;top:89px;width:195px}
.cat .photo{width:195px;height:134px}
.cat h4{margin-top:12px;font-size:12px;font-weight:700;color:var(--white)}
.cat p{margin-top:4px;font-size:12px;color:#d8e9fa}

/* project listings */
.projects{position:absolute;left:0;width:1200px}
.featured{top:890px;height:711px;background:var(--white)}
.launches{top:1601px;height:388px;background:var(--panel)}
.projects .section-title{color:#333}
.arrow{position:absolute}
.card{position:absolute;width:195px;height:260px;background:var(--white);box-shadow:0 4px 10px rgba(0,0,0,.12)}
.card .photo{position:absolute;left:0;top:0;width:195px;height:162px}
.city-tag{position:absolute;left:57px;top:72px;width:82px;height:22px;line-height:22px;background:var(--blue);color:var(--white);font-size:12px;font-weight:700;text-align:center}
.card .loc{position:absolute;top:172px;width:100%;text-align:center;font-size:13px;color:#444}
.card .name{position:absolute;top:192px;width:100%;text-align:center;font-size:16px;font-weight:700;color:#222}
.card .visit{position:absolute;left:35px;top:219px;width:126px;height:24px;line-height:24px;background:var(--navy);color:var(--white);font-size:10.5px;font-weight:700;text-align:center;letter-spacing:.3px}

/* mail alert */
.mail-alert{position:absolute;left:0;top:1989px;width:1200px;height:130px;background:var(--black-band);color:var(--white)}
.mail-alert .lead{position:absolute;top:20px;width:1200px;text-align:center;font-size:16px}
.mail-alert .lead b{font-weight:700}
.mail-alert .lead svg{vertical-align:-2px;margin-right:8px}
.dark-input{position:absolute;top:59px;height:32px;background:#3a3a3a;color:#e0e0e0;font-size:12.5px;line-height:32px;padding:0 10px}
.dark-input svg{position:absolute;right:10px;top:10px}
.subscribe{position:absolute;left:919px;top:59px;width:115px;height:32px;line-height:32px;background:var(--blue);color:var(--white);font-weight:700;font-size:13px;text-align:center}
.hint{position:absolute;top:101px;font-size:11.5px;color:#bdbdbd}

/* footer */
.site-footer{position:absolute;left:0;top:2119px;width:1200px;height:449px;background:var(--footer)}
.foot-head{position:absolute;top:45px;font-size:12.5px;font-weight:700;color:var(--blue)}
.link-list{position:absolute;left:166px;top:82px;list-style:none;font-size:12.5px;color:#333;line-height:27.5px}
.editor p{position:absolute;font-size:12.5px;color:#333;line-height:22px;width:222px}
.editor .more{color:var(--blue)}
.editor .url{position:absolute;left:358px;top:198px;font-size:12.5px;font-weight:700;color:var(--blue)}
.wizards{position:absolute;left:613px;top:38px;width:195px;height:295px;background:var(--blue);color:var(--white);padding:10px 10px}
.wizards h5{font-size:12.5px;font-weight:700}
.wizards p{margin-top:14px;font-size:11.5px;line-height:16px;color:#eaf3fc}
.w-input{margin-top:8px;height:20px;background:#5ea6e6;font-size:9.5px;line-height:20px;padding:0 8px;color:#dfeefb}
.w-input.tall{height:38px}
.w-btn{margin-top:8px;display:inline-block;background:var(--navy);font-size:10px;padding:4px 8px;color:var(--white)}
.contact p{position:absolute;left:835px;font-size:12.5px;color:#333;line-height:22px}
.foot-brand{position:absolute;left:170px;top:386px;display:flex;align-items:center;gap:8px;font-weight:900;font-size:22px;color:#555}
.foot-brand .brand-dot{width:22px;height:22px;background:#555}
.social{position:absolute;left:865px;top:372px;display:flex;gap:15px}
.social span{width:19px;height:19px;background:#666;border-radius:2px}
.copyright{position:absolute;left:615px;top:399px;width:419px;text-align:right;font-size:12.5px;color:#333}
</style>
</head>
<body>

<header class="site-header">
  <div class="brand"><span class="brand-dot"></span>lotstallmart</div>
  <nav class="top-nav">
    <a style="left:514px;width:142px">Advertise with Us</a>
    <a style="left:668px;width:97px">Listings Alert</a>
    <a style="left:776px;width:106px">Mart Wizards</a>
    <a class="login" style="left:890px;width:144px">ADVERTISER LOGIN</a>
  </nav>
</header>

<section class="hero">
  <div class="abs" style="left:0;top:0;width:1200px;height:504px" role="img" aria-label="Banner photo: a smiling family shopping in a retail mall"></div>
  <div class="hero-dots"><span class="on"></span><span></span><span></span><span></span><span></span></div>
  <div class="mode-tabs"><div class="sale">Sale</div><div class="rent">Rent \ Lease</div></div>
  <form class="search-panel">
    <div class="field" style="top:35px">Type Of Space Category<svg width="10" height="6"><path d="M0 0h10L5 6z" fill="#555"/></svg></div>
    <div class="field" style="top:96px">City<svg width="10" height="6"><path d="M0 0h10L5 6z" fill="#555"/></svg></div>
    <div class="field" style="top:162px">Locality<svg width="10" height="6"><path d="M0 0h10L5 6z" fill="#555"/></svg></div>
    <div class="field" style="top:227px">Transaction Type<svg width="10" height="6"><path d="M0 0h10L5 6z" fill="#555"/></svg></div>
    <div class="field" style="top:292px">Area Range<svg width="10" height="6"><path d="M0 0h10L5 6z" fill="#555"/></svg></div>
    <div class="search-btn">SEARCH</div>
  </form>
</section>

<section class="categories">
  <h2 class="section-title">THE PROPERTIES CATEGORIES</h2>
  <div class="cat" style="left:166px"><div class="photo" role="img" aria-label="Photo: shopper with bags in a retail mall" style="background:linear-gradient(135deg,#3a2b24,#b08a6a)"></div><h4>Retail Malls</h4><p>Centrally Air-Conditioned</p></div>
  <div class="cat" style="left:389px"><div class="photo" role="img" aria-label="Photo: shoppers walking through a shopping complex" style="background:linear-gradient(135deg,#2d2a2a,#8a7a6a)"></div><h4>Shopping Complexes</h4><p>Non Air-Conditioned Building</p></div>
  <div class="cat" style="left:613px"><div class="photo" role="img" aria-label="Photo: shopper with bags on a high street" style="background:linear-gradient(135deg,#d9d0c4,#c77a3a)"></div><h4>High-Street Shops</h4><p>Road Facing Retail</p></div>
  <div class="cat" style="left:837px"><div class="photo" role="img" aria-label="Photo: shopper holding colourful shopping bags" style="background:linear-gradient(135deg,#f4f4f4,#e28a3c)"></div><h4>Retail &nbsp;Warehouses</h4><p>Back-end Ratail Storage</p></div>
</section>

<section class="projects featured">
  <h2 class="section-title" style="top:46px">FEATURED PROJECTS</h2>
  <svg class="arrow" style="left:166px;top:51px" width="9" height="14"><path d="M8 1L2 7l6 6" stroke="#222" stroke-width="2.2" fill="none"/></svg>
  <svg class="arrow" style="left:1024px;top:51px" width="9" height="14"><path d="M1 1l6 6-6 6" stroke="#222" stroke-width="2.2" fill="none"/></svg>

  <article class="card" style="left:166px;top:117px"><div class="photo" role="img" aria-label="Photo: shopping complex building exterior" style="background:linear-gradient(180deg,#a7c1d9,#a58d6d)"></div><span class="city-tag">SURAT</span><div class="loc">Corvana,Althan</div><div class="name">Shopping Complex</div><div class="visit">VISIT ALL LISITINGS</div></article>
  <article class="card" style="left:389px;top:117px"><div class="photo" role="img" aria-label="Photo: mall interior with shopfronts" style="background:linear-gradient(180deg,#4a3a30,#9a7a5a)"></div><span class="city-tag">SURAT</span><div class="loc">Corvana,Althan</div><div class="name">Shopping Complex</div><div class="visit">VISIT ALL LISITINGS</div></article>
  <article class="card" style="left:613px;top:117px"><div class="photo" role="img" aria-label="Photo: multi-level mall atrium" style="background:linear-gradient(180deg,#6a5a4a,#c2a888)"></div><span class="city-tag">SURAT</span><div class="loc">Corvana,Althan</div><div class="name">Shopping Complex</div><div class="visit">VISIT ALL LISITINGS</div></article>
  <article class="card" style="left:837px;top:117px"><div class="photo" role="img" aria-label="Photo: modern commercial towers" style="background:linear-gradient(180deg,#b9d0e2,#7a9a8a)"></div><span class="city-tag">SURAT</span><div class="loc">Corvana,Althan</div><div class="name">Shopping Complex</div><div class="visit">VISIT ALL LISITINGS</div></article>

  <article class="card" style="left:166px;top:408px"><div class="photo" role="img" aria-label="Photo: mall facade at dusk" style="background:linear-gradient(180deg,#8aa2ba,#5a5046)"></div><span class="city-tag">SURAT</span><div class="loc">Corvana,Althan</div><div class="name">Shopping Complex</div><div class="visit">VISIT ALL LISITINGS</div></article>
  <article class="card" style="left:389px;top:408px"><div class="photo" role="img" aria-label="Photo: storefront entrance with signage" style="background:linear-gradient(180deg,#5a7a8a,#c7b79a)"></div><span class="city-tag">SURAT</span><div class="loc">Corvana,Althan</div><div class="name">Shopping Complex</div><div class="visit">VISIT ALL LISITINGS</div></article>
  <article class="card" style="left:613px;top:408px"><div class="photo" role="img" aria-label="Photo: illuminated cinema and mall facade at night" style="background:linear-gradient(180deg,#2a1a12,#c25a1a)"></div><span class="city-tag">SURAT</span><div class="loc">Corvana,Althan</div><div class="name">Shopping Complex</div><div class="visit">VISIT ALL LISITINGS</div></article>
  <article class="card" style="left:837px;top:408px"><div class="photo" role="img" aria-label="Photo: glass mall building exterior" style="background:linear-gradient(180deg,#6a8ab0,#3a5a80)"></div><span class="city-tag">SURAT</span><div class="loc">Corvana,Althan</div><div class="name">Shopping Complex</div><div class="visit">VISIT ALL LISITINGS</div></article>
</section>

<section class="projects launches">
  <h2 class="section-title" style="top:42px">NEW LAUNCHES</h2>
  <svg class="arrow" style="left:166px;top:47px" width="9" height="14"><path d="M8 1L2 7l6 6" stroke="#222" stroke-width="2.2" fill="none"/></svg>
  <svg class="arrow" style="left:1024px;top:47px" width="9" height="14"><path d="M1 1l6 6-6 6" stroke="#222" stroke-width="2.2" fill="none"/></svg>

  <article class="card" style="left:166px;top:94px"><div class="photo" role="img" aria-label="Rendering: new shopping complex with plaza" style="background:linear-gradient(180deg,#7a4a3a,#b0a090)"></div><span class="city-tag">SURAT</span><div class="loc">Corvana,Althan</div><div class="name">Shopping Complex</div><div class="visit">VISIT ALL LISITINGS</div></article>
  <article class="card" style="left:389px;top:94px"><div class="photo" role="img" aria-label="Rendering: high-rise retail tower at night" style="background:linear-gradient(180deg,#1a3a6a,#3a6a8a)"></div><span class="city-tag">SURAT</span><div class="loc">Corvana,Althan</div><div class="name">Shopping Complex</div><div class="visit">VISIT ALL LISITINGS</div></article>
  <article class="card" style="left:613px;top:94px"><div class="photo" role="img" aria-label="Rendering: low-rise commercial block" style="background:linear-gradient(180deg,#9ac0e0,#b07a5a)"></div><span class="city-tag">SURAT</span><div class="loc">Corvana,Althan</div><div class="name">Shopping Complex</div><div class="visit">VISIT ALL LISITINGS</div></article>
  <article class="card" style="left:837px;top:94px"><div class="photo" role="img" aria-label="Rendering: retail street with parking" style="background:linear-gradient(180deg,#a8cae6,#8a8a7a)"></div><span class="city-tag">SURAT</span><div class="loc">Corvana,Althan</div><div class="name">Shopping Complex</div><div class="visit">VISIT ALL LISITINGS</div></article>
</section>

<section class="mail-alert">
  <p class="lead"><svg width="16" height="12"><rect x="0" y="0" width="16" height="12" rx="1" fill="var(--blue)"/><path d="M0 1l8 6 8-6" stroke="#1e1e1e" stroke-width="1.5" fill="none"/></svg><b>Mail Listing Alert :</b> Subscribe &nbsp;for Fortnightly Email update on New Listings @ Lotstallmart</p>
  <div class="dark-input" style="left:166px;width:233px">Enter Your E-Mail Address<svg width="8" height="12"><path d="M0 5h8L4 0zM0 7h8L4 12z" fill="#888"/></svg></div>
  <div class="dark-input" style="left:413px;width:232px">Select Options<svg width="8" height="12"><path d="M0 5h8L4 0zM0 7h8L4 12z" fill="#888"/></svg></div>
  <div class="dark-input" style="left:659px;width:248px">Agra<svg width="8" height="12"><path d="M0 5h8L4 0zM0 7h8L4 12z" fill="#888"/></svg></div>
  <div class="subscribe">SUBSCRIBE</div>
  <p class="hint" style="left:413px">(Select retail format of interest)</p>
  <p class="hint" style="left:659px">(Select cities of interest)</p>
</section>

<footer class="site-footer">
  <h5 class="foot-head" style="left:166px">About Stallway Central</h5>
  <ul class="link-list">
    <li>About Us</li><li>Privacy Policy</li><li>Terms of Use</li><li>Contact Us</li><li>Site Map</li><li>Retail Malls</li><li>Shopping Complex</li><li>High Street Shops</li><li>Retail Warehouses</li>
  </ul>

  <div class="editor">
    <h5 class="foot-head" style="left:361px">Editor's Choice</h5>
    <p style="left:361px;top:84px">A "Select" Listing of Retail Properties Handpicked by our Editors based on their own positive evaluation on parameters &amp; attributes &nbsp;.... <span class="more">More...</span></p>
    <span class="url">www.lotstallmart.com</span>
    <p style="left:358px;top:232px">Lotstallmart.com - About Us Lotstallmart.com is a Specialised Web based platform for Retail Space, featuring properties .... <span class="more">More...</span></p>
  </div>

  <div class="wizards">
    <h5>Mart Wizards</h5>
    <p>Post your Retail Space requirement with us and our experts shall get back with suitable options and even help you in your transaction. This is a Free Service!</p>
    <div class="w-input">Enter Your E-mail Address</div>
    <div class="w-input">Mobile</div>
    <div class="w-input tall">Add Description Of Requirement</div>
    <span class="w-btn">Subscribe</span>
  </div>

  <div class="contact">
    <h5 class="foot-head" style="left:835px">Contact</h5>
    <p style="top:86px">Stallway Central<br>Unit 218, 2nd Floor,<br>Lorem Ipsum is simply,<br>Sector-x, Gurgaon - 122002</p>
    <p style="top:206px">Phone : 000-000-0000<br>Fax : 000 - 000 - 0000</p>
  </div>

  <div class="social"><span></span><span></span><span></span><span></span><span></span></div>
  <p class="copyright">Copyright © 2015Stallway Central.com. All rights reserved</p>
  <div class="foot-brand"><span class="brand-dot"></span>lotstallmart</div>
</footer>

</body>
</html>
```